Veldmark Supplies Business Card

Professional business card that stand out to our potential customers. Front and back with clean modern design

Industry/Entity Type

Oil and gas

Contact Information for Business Card

Name, address, website , office phone and cell number

Requirements
Must have
• Editable files for each employee

```html
<!DOCTYPE html>
<html lang="en">
<head>
<meta charset="utf-8">
<title>Veldmark Supplies – Business Card</title>
<link href="https://fonts.googleapis.com/css2?family=Montserrat:wght@400;500;800&display=swap" rel="stylesheet">
<style>
  :root {
    --page-bg: #d9d9d9;
    --card-bg: #2b2b2d;
    --card-back-dark: #1c1c1e;
    --card-back-light: #4a4a4c;
    --brand-red: #e41e26;
    --brand-blue: #12b0d6;
    --text-light: #f2f2f2;
  }
  * { margin: 0; padding: 0; box-sizing: border-box; }
  html, body { width: 1200px; height: 856px; overflow: hidden; }
  body {
    background: var(--page-bg);
    font-family: "Montserrat", sans-serif;
    display: flex;
    flex-direction: column;
    align-items: center;
    justify-content: center;
    gap: 44px;
  }
  .card {
    width: 560px;
    height: 320px;
    position: relative;
    overflow: hidden;
    box-shadow: 0 10px 28px rgba(0,0,0,.28);
  }
  /* Front */
  .card-front { background: var(--card-bg); display: flex; }
  .brand-side {
    width: 290px;
    display: flex;
    align-items: center;
    justify-content: center;
    gap: 12px;
  }
  .brand-square { width: 22px; height: 22px; background: var(--brand-red); }
  .brand-name {
    color: var(--text-light);
    font-weight: 800;
    font-size: 21px;
    letter-spacing: 1px;
    text-transform: uppercase;
  }
  .divider { width: 2px; background: var(--brand-red); margin: 44px 0; }
  .contact-side { padding: 46px 0 0 24px; color: var(--text-light); }
  .person-name {
    color: var(--brand-red);
    font-weight: 800;
    font-size: 21px;
    letter-spacing: .5px;
    text-transform: uppercase;
  }
  .person-title { font-size: 13px; font-weight: 500; margin-top: 2px; }
  .address { font-size: 12px; line-height: 1.4; margin-top: 14px; }
  .contact-list { list-style: none; margin-top: 12px; }
  .contact-list li {
    display: flex;
    align-items: center;
    gap: 9px;
    font-size: 12px;
    line-height: 1;
    margin-bottom: 8px;
  }
  .contact-icon {
    width: 16px; height: 16px;
    background: var(--brand-red);
    display: flex; align-items: center; justify-content: center;
    flex-shrink: 0;
  }
  /* Back */
  .card-back {
    background: var(--card-back-dark);
  }
  .back-pattern {
    position: absolute; inset: 0;
    background: linear-gradient(120deg, var(--card-back-light) 0%, #333335 45%, var(--card-back-dark) 75%, #111 100%);
  }
  .back-brand {
    position: absolute;
    right: 40px;
    top: 50%;
    transform: translateY(-50%);
    display: flex;
    align-items: center;
    gap: 10px;
  }
  .back-brand .brand-name { font-size: 15px; }
  .back-brand .brand-square { width: 16px; height: 16px; }
</style>
</head>
<body>

  <section class="card card-front" aria-label="Business card front">
    <div class="brand-side">
      <span class="brand-square"></span>
      <span class="brand-name">Veldmark Supplies</span>
    </div>
    <div class="divider"></div>
    <div class="contact-side">
      <h1 class="person-name">Dane Holloway</h1>
      <p class="person-title">President</p>
      <p class="address">4820 Calder Ave, Ste<br>210, Midland, TX 79701</p>
      <ul class="contact-list">
        <li>
          <span class="contact-icon">
            <svg width="10" height="10" viewBox="0 0 10 10"><path d="M2 1h2l1 2-1.2 1a5 5 0 0 0 2.2 2.2L7 5l2 1v2a1 1 0 0 1-1 1A7 7 0 0 1 1 2a1 1 0 0 1 1-1z" fill="#fff"/></svg>
          </span>
          432-555-0148
        </li>
        <li>
          <span class="contact-icon">
            <svg width="10" height="10" viewBox="0 0 10 10"><rect x="2.5" y="0.5" width="5" height="9" rx="1" fill="none" stroke="#fff"/><circle cx="5" cy="8" r=".6" fill="#fff"/></svg>
          </span>
          000-000-9999
        </li>
        <li>
          <span class="contact-icon">
            <svg width="10" height="10" viewBox="0 0 10 10"><rect x="0.5" y="2" width="9" height="6" fill="none" stroke="#fff"/><path d="M.5 2 5 5.5 9.5 2" fill="none" stroke="#fff"/></svg>
          </span>
          info@example-youremail.com
        </li>
        <li>
          <span class="contact-icon">
            <svg width="10" height="10" viewBox="0 0 10 10"><circle cx="5" cy="5" r="4.2" fill="none" stroke="#fff"/><ellipse cx="5" cy="5" rx="1.8" ry="4.2" fill="none" stroke="#fff" stroke-width=".8"/><path d="M.8 5h8.4" stroke="#fff" stroke-width=".8"/></svg>
          </span>
          www.example-yourwebsite.com
        </li>
      </ul>
    </div>
  </section>

  <section class="card card-back" aria-label="Business card back">
    <div class="back-pattern" role="img" aria-label="Repeating glossy brand-mark pattern on dark background"></div>
    <div class="back-brand">
      <span class="brand-square"></span>
      <span class="brand-name">Veldmark Supplies</span>
    </div>
  </section>

</body>
</html>
```